Letterhead Design Project

Letterhead for a Consultant Cardiologist in Adelaide Australia. Should be very classy, mature and imposing. I would prefer colours that portray confidence, gentleness and serenity.

The PDF attached is for you to see the details that will be on the letterhead and not the design which is extremely poor!

Target Market(s)

Health professionals especially medical doctors

Industry/Entity Type

Consultant

```html
<!DOCTYPE html>
<html lang="en">
<head>
<meta charset="utf-8">
<title>Dr Obinna K. Nwachukwu – Letterhead</title>
<link href="https://fonts.googleapis.com/css2?family=Tinos:wght@400;700&family=Open+Sans:wght@300;400;600&display=swap" rel="stylesheet">
<style>
  :root {
    --red: #d11f27;
    --red-dark: #9e141a;
    --ink: #2a2a2a;
    --grey-text: #8a8a8a;
    --band-light: #f4f4f4;
    --band-mid: #d8d8d8;
    --band-dark: #a9a9a9;
    --paper: #ffffff;
  }
  * { margin: 0; padding: 0; box-sizing: border-box; }
  html, body { width: 849px; height: 1200px; overflow: hidden; background: var(--paper); }
  .letterhead { position: relative; width: 849px; height: 1200px; background: var(--paper); overflow: hidden; }

  .header {
    position: absolute; left: 0; top: 0; width: 100%; height: 158px;
    background: linear-gradient(100deg, var(--band-light) 0%, var(--band-mid) 55%, var(--band-dark) 100%);
  }
  .header-rule {
    position: absolute; left: 0; top: 158px; width: 100%; height: 7px;
    background: linear-gradient(90deg, var(--red-dark), var(--red) 40%, var(--red));
  }
  .brand-dot {
    position: absolute; left: 200px; top: 22px; width: 90px; height: 90px;
    border-radius: 50%; background: var(--red);
  }
  .identity { position: absolute; left: 316px; top: 26px; font-family: "Tinos", serif; }
  .identity .name { font-size: 25px; font-weight: 700; color: var(--ink); line-height: 1.2; }
  .identity .credentials { font-size: 15px; color: var(--ink); margin-top: 4px; letter-spacing: 0.5px; }
  .identity .specialty { font-size: 16px; color: var(--red); margin-top: 3px; }

  .contacts {
    position: absolute; left: 666px; top: 416px; width: 175px;
    font-family: "Open Sans", sans-serif; font-size: 11px; line-height: 14.5px;
    color: var(--grey-text); font-weight: 300; white-space: nowrap;
  }
  .contacts .location { margin-bottom: 15px; }
  .contacts .heading { color: var(--red); font-weight: 400; }

  .footer {
    position: absolute; left: 0; bottom: 0; width: 100%; height: 34px;
    background: linear-gradient(100deg, var(--band-light) 0%, var(--band-mid) 55%, var(--band-dark) 100%);
  }
  .footer-rule {
    position: absolute; left: 0; bottom: 34px; width: 100%; height: 5px;
    background: linear-gradient(90deg, var(--red-dark), var(--red));
  }
</style>
</head>
<body>
<div class="letterhead">
  <header class="header">
    <div class="brand-dot"></div>
    <div class="identity">
      <div class="name">Dr Obinna K. Nwachukwu</div>
      <div class="credentials">M.B.B.S, F.M.C.P, F.R.A.C.P</div>
      <div class="specialty">Cardiologist</div>
    </div>
  </header>
  <div class="header-rule"></div>

  <aside class="contacts">
    <div class="location">
      <div class="heading">Consulting<br>Riverside Specialist Centre</div>
      48 Harbour Road<br>
      Harbourton SA 5012<br>
      T: 8312 4470<br>
      F: 8312 4471
    </div>
    <div class="location">
      <div class="heading">Provider No.: 4067321Y<br>Northgate Cardiology</div>
      &amp; Specialist Clinic<br>
      Westmere Private<br>
      Hospital<br>
      19 Linden Road<br>
      Eastvale SA 5113<br>
      T: 8390 2215<br>
      F: 8390 2216<br>
      E: info@ngcardio.com.au<br>
      Provider No.: 4067322K
    </div>
    <div class="location">
      <div class="heading">Port Linton Hospital</div>
      62 Harbour Road<br>
      Port Linton 5701<br>
      T: 8651 3300<br>
      F: 8312 4471<br>
      Provider No.: 4067323B
    </div>
  </aside>

  <div class="footer-rule"></div>
  <footer class="footer"></footer>
</div>
</body>
</html>
```